PSD Designs needed to give to my Developer

Hello, I need PSD files to give to my programmer for the creation of my new website. The website is for KORVA lane, a new clothing company based in Chicago, IL. We sell womens, mens and kids fashion. We specialize in jackets, outerwear and sweaters, but we sell clothing from every category, I have someone working on the logo, so I can't include it for reference. However, I have included 2 reference sites as well as a PDF of how the 2 reference sites could be merged together. The main company color should be blue (hence the name KORVA lane), and the overall feel of the site should be FUN. It should communicate: This is where you want to shop if you want a FUN, HAPPY experience. I need the Home Page file designed very quickly. Whoever is awarded this job will immediately continue working with me to design the other 8 pages. I will pay for all pages. The amount I am offering is for this one page only, and I will pay you additional to design all other 8 pages. Thank you for your time and I will be picking the best design so that we can immediately build a great relationship and work through the rest of the project.

Industry/Entity Type

Apparel Store

Number of Pages Required

1 page

Font styles to use
Sans Serif

Colors
33a6d7
0492cd
ffffff

Requirements
Must have
• I have included all notes in the project description so please check there. My project must communicate: Fun and Happy Design. Even tho I have chosen a few variations of blue below, I still want the designer to incorporate other colors as necessary to acheive the desired look.
Should not have
• It should have a boring, childish feel

```html
<!DOCTYPE html>
<html lang="en">
<head>
<meta charset="utf-8">
<title>KORVA lane — Home</title>
<link rel="stylesheet" href="https://fonts.googleapis.com/css2?family=Lato:wght@400;700;900&display=swap">
<style>
  :root {
    --blue-bar: #2f97d3;
    --blue-dark: #1c72b8;
    --blue-brand: #1a86c8;
    --blue-story: #0e6fc6;
    --ink: #111111;
    --nav-ink: #555b61;
    --foot-ink: #6b6f73;
    --white: #ffffff;
    --hero-bg-top: #f3f3f3;
    --hero-bg-bottom: #e9e8e7;
  }
  * { box-sizing: border-box; margin: 0; padding: 0; }
  html, body { width: 962px; height: 1200px; overflow: hidden; }
  body { font-family: "Lato", sans-serif; background: var(--white); position: relative; }

  .promo-bar { position: absolute; left: 0; top: 0; width: 962px; height: 32px; background: var(--blue-bar); }
  .promo-text { position: absolute; left: 140px; top: 8px; font-size: 12px; font-weight: 700; color: var(--white); }
  .stylist-login { position: absolute; left: 734px; top: 0; width: 107px; height: 31px; background: var(--blue-dark); color: var(--white); font-size: 12px; font-weight: 700; text-align: center; line-height: 28px; }

  .site-header { position: absolute; left: 0; top: 32px; width: 962px; height: 55px; background: #fafafa; border-bottom: 1px solid #ececec; }
  .main-nav { position: absolute; left: 109px; top: 31px; display: flex; gap: 26px; font-size: 12px; color: var(--nav-ink); letter-spacing: 0.2px; }
  .main-nav .active { color: #2b2f33; }
  .brand-name { position: absolute; left: 677px; top: 18px; font-size: 31px; font-weight: 400; color: var(--blue-brand); }

  .hero { position: absolute; left: 0; top: 87px; width: 962px; height: 440px; background: linear-gradient(180deg, var(--hero-bg-top), var(--hero-bg-bottom)); }
  .hero-photo { position: absolute; left: 130px; top: 10px; width: 314px; height: 430px;
    background:
      radial-gradient(ellipse 22% 14% at 52% 15%, #8f7f72 0%, rgba(143,127,114,0) 100%),
      radial-gradient(ellipse 50% 42% at 50% 58%, #a8743f 0%, #b07c46 55%, rgba(176,124,70,0) 100%),
      linear-gradient(180deg, rgba(243,243,243,0) 0%, rgba(233,232,231,0) 85%, #ebe9e6 100%); }
  .slider-arrow { position: absolute; top: 178px; width: 40px; height: 40px; }
  .slider-arrow.prev { left: 71px; }
  .slider-arrow.next { left: 851px; }
  .hero-title { position: absolute; left: 479px; top: 121px; font-size: 42px; line-height: 40px; font-weight: 900; color: var(--blue-brand); letter-spacing: 0.5px; }
  .hero-sub { position: absolute; left: 479px; top: 213px; font-size: 23px; color: var(--ink); }
  .shop-now { position: absolute; left: 477px; top: 250px; width: 76px; height: 76px; border: 2px solid var(--blue-brand); border-radius: 50%; color: var(--blue-brand); font-size: 15px; font-weight: 700; line-height: 18px; text-align: center; padding-top: 19px; }

  .our-story { position: absolute; left: 0; top: 527px; width: 962px; height: 315px;
    background:
      radial-gradient(ellipse 22% 45% at 52% 40%, rgba(70,130,200,0.55) 0%, rgba(70,130,200,0) 100%),
      linear-gradient(90deg, #1a62ad 0%, #1d6cbf 25%, var(--blue-story) 55%, #1678cc 100%);
    color: var(--white); text-align: center; }
  .story-title { position: absolute; left: 0; width: 962px; top: 70px; font-size: 32px; font-weight: 700; }
  .story-text { position: absolute; left: 191px; width: 582px; top: 119px; font-size: 14.2px; line-height: 22.5px; }
  .story-button { position: absolute; left: 425px; top: 209px; width: 119px; height: 32px; border: 2px solid var(--white); font-size: 12px; font-weight: 700; line-height: 28px; }

  .tile { position: absolute; top: 842px; height: 295px; color: var(--white); text-align: center; }
  .tile-shop { left: 0; width: 478px;
    background:
      radial-gradient(ellipse 30% 35% at 20% 70%, #c8a43a 0%, rgba(200,164,58,0) 100%),
      radial-gradient(ellipse 30% 40% at 82% 65%, #d05a8e 0%, rgba(208,90,142,0) 100%),
      radial-gradient(ellipse 30% 35% at 55% 30%, #c43a45 0%, rgba(196,58,69,0) 100%),
      linear-gradient(135deg, #6d83a6 0%, #a85a68 50%, #b8344a 100%); }
  .tile-join { left: 478px; width: 484px;
    background:
      radial-gradient(ellipse 28% 40% at 55% 55%, #8a7458 0%, rgba(138,116,88,0) 100%),
      linear-gradient(135deg, #4e4436 0%, #5f5040 50%, #3f3a35 100%); }
  .tile-shade { position: absolute; inset: 0; background: rgba(20, 30, 50, 0.2); }
  .tile-label { position: absolute; left: 0; right: 0; font-weight: 700; }
  .tile-shop .tile-label { top: 120px; font-size: 27px; }
  .tile-join .tile-label.small { top: 110px; font-size: 22px; }
  .tile-join .tile-label.large { top: 137px; font-size: 26px; }

  .site-footer { position: absolute; left: 0; top: 1137px; width: 962px; height: 63px; background: var(--white); }
  .copyright { position: absolute; left: 109px; top: 20px; font-size: 12px; color: var(--foot-ink); }
  .social-links { position: absolute; left: 733px; top: 13px; width: 112px; height: 30px; }
</style>
</head>
<body>
  <div class="promo-bar">
    <p class="promo-text">Pop-up your own KORVA Corner for ONLY $99</p>
    <div class="stylist-login">Stylist Login</div>
  </div>

  <header class="site-header">
    <nav class="main-nav">
      <span class="active">HOME</span>
      <span>GET TO KNOW US</span>
      <span>WHY KORVA?</span>
      <span>HOST A POP-UP</span>
      <span>BECOME A STYLIST</span>
    </nav>
    <div class="brand-name">KORVA lane</div>
  </header>

  <section class="hero">
    <div class="hero-photo" role="img" aria-label="Photo: man with glasses and grey beard in a tan suede bomber jacket and white trousers"></div>
    <svg class="slider-arrow prev" viewBox="0 0 40 40" aria-label="Previous slide">
      <circle cx="20" cy="20" r="19" fill="none" stroke="#111" stroke-width="1.6"/>
      <path d="M23 13 L16 20 L23 27" fill="none" stroke="#111" stroke-width="2.4" stroke-linecap="round" stroke-linejoin="round"/>
    </svg>
    <svg class="slider-arrow next" viewBox="0 0 40 40" aria-label="Next slide">
      <circle cx="20" cy="20" r="19" fill="none" stroke="#111" stroke-width="1.6"/>
      <path d="M17 13 L24 20 L17 27" fill="none" stroke="#111" stroke-width="2.4" stroke-linecap="round" stroke-linejoin="round"/>
    </svg>
    <h1 class="hero-title">LIMITED<br>INVENTORY</h1>
    <p class="hero-sub">that’s onlyavailable for ONE week!</p>
    <div class="shop-now">SHOP<br>NOW</div>
  </section>

  <section class="our-story" role="img" aria-label="Blue-toned photo of a woman in a knit sweater leaning by a door">
    <h2 class="story-title">OUR STORY</h2>
    <p class="story-text">elementum elit at tellus nec ultricies sit amet porttitor mattis enim In massa libero<br>interdum nec interdum vel blandit sed nulla In ullamcorper est eget tempor cursus neque<br>mi consectetuer mi a ultricies massa est sed nisl Class aptent</p>
    <div class="story-button">CLICK HERE</div>
  </section>

  <section class="tile tile-shop" role="img" aria-label="Photo: three smiling kids in colourful winter hats and scarves">
    <div class="tile-shade"></div>
    <p class="tile-label">SHOP</p>
  </section>
  <section class="tile tile-join" role="img" aria-label="Photo: woman in a shearling coat and beanie walking in the snow">
    <div class="tile-shade"></div>
    <p class="tile-label small">BE HAPPIER</p>
    <p class="tile-label large">JOIN THE MOVEMENT</p>
  </section>

  <footer class="site-footer">
    <p class="copyright">© 2018 Company Name&nbsp; All right reserved&nbsp; Terms of Use</p>
    <svg class="social-links" viewBox="0 0 112 30" aria-label="Social media links">
      <circle cx="14" cy="15" r="13" fill="none" stroke="#1a86c8" stroke-width="1.5"/>
      <circle cx="42" cy="15" r="13" fill="none" stroke="#1a86c8" stroke-width="1.5"/>
      <circle cx="70" cy="15" r="13" fill="none" stroke="#1a86c8" stroke-width="1.5"/>
      <circle cx="98" cy="15" r="13" fill="none" stroke="#1a86c8" stroke-width="1.5"/>
    </svg>
  </footer>
</body>
</html>
```